Tech business card design

We need an amazing business card design for our new business 'Pexla' a marketing tech startup based in Sydney, Australia. We provide an online marketplace for businesses to search and buy advertising media, connect with service providers and learn more about marketing. We wish to communicate 'cool tech', reliability and professionalism and design based around our logo.

Target Market(s)

Business Owners

Contact Information for Business Card

Name
Position
Email Address
Website
Phone Number

Font styles to use
Other font styles liked:
• Avenir & Avenir Next

Colors

Designer to choose colors to be used in the design.

```html
<!DOCTYPE html>
<html lang="en">
<head>
<meta charset="utf-8">
<title>Pexla Business Card</title>
<link rel="stylesheet" href="https://fonts.googleapis.com/css2?family=Roboto:wght@400;700;900&display=swap">
<style>
  :root {
    --backdrop: #211f45;
    --navy: #232250;
    --paper: #f4f4f4;
    --strip: #d6d6dc;
    --text-grey: #5a5a62;
    --back-light: #2c2a5a;
    --back-dark: #24224c;
    --white: #ffffff;
  }
  * { margin: 0; padding: 0; box-sizing: border-box; }
  html, body {
    width: 1200px;
    height: 986px;
    overflow: hidden;
    background: var(--backdrop);
    font-family: "Roboto", sans-serif;
  }
  .canvas { position: relative; width: 1200px; height: 986px; }
  .card {
    position: absolute;
    left: 341px;
    width: 518px;
    height: 296px;
    overflow: hidden;
  }
  .card--front { top: 160px; background: var(--paper); }
  .card--back { top: 530px; }

  .wordmark {
    position: absolute;
    left: 39px;
    top: 44px;
    font-size: 72px;
    font-weight: 900;
    line-height: 1;
    letter-spacing: -1px;
    color: var(--navy);
  }
  .pattern-strip {
    position: absolute;
    left: 360px;
    top: 0;
    width: 158px;
    height: 296px;
    background: linear-gradient(180deg, var(--strip), #dcdce1);
  }
  .person { position: absolute; left: 42px; top: 158px; }
  .person__name {
    font-size: 21px;
    font-weight: 700;
    color: var(--navy);
    line-height: 1.2;
  }
  .person__role {
    font-size: 14px;
    font-weight: 400;
    color: var(--text-grey);
    line-height: 1.2;
  }
  .contact { position: absolute; left: 42px; top: 213px; list-style: none; }
  .contact__item {
    display: flex;
    align-items: center;
    gap: 6px;
    height: 17.6px;
    font-size: 12.5px;
    color: var(--text-grey);
  }
  .contact__icon { width: 11px; height: 11px; fill: var(--navy); flex: none; }

  .back-pattern {
    position: absolute;
    inset: 0;
    background: linear-gradient(135deg, var(--back-light), var(--back-dark));
  }
  .back-wordmark {
    position: absolute;
    left: 404px;
    top: 126px;
    font-size: 30px;
    font-weight: 900;
    line-height: 1;
    color: var(--white);
  }
</style>
</head>
<body>
<main class="canvas">
  <section class="card card--front" aria-label="Business card front">
    <div class="wordmark">Pexla</div>
    <div class="pattern-strip" role="img" aria-label="Faint repeated brand-name pattern"></div>
    <div class="person">
      <p class="person__name">Marcus Ellery</p>
      <p class="person__role">Managing Director</p>
    </div>
    <ul class="contact">
      <li class="contact__item">
        <svg class="contact__icon" viewBox="0 0 24 24" aria-hidden="true"><path d="M6.6 10.8a15.1 15.1 0 0 0 6.6 6.6l2.2-2.2a1 1 0 0 1 1-.25 11.4 11.4 0 0 0 3.6.6 1 1 0 0 1 1 1V20a1 1 0 0 1-1 1A17 17 0 0 1 3 4a1 1 0 0 1 1-1h3.5a1 1 0 0 1 1 1c0 1.25.2 2.45.6 3.6a1 1 0 0 1-.25 1z"/></svg>
        <span>123 456 7890</span>
      </li>
      <li class="contact__item">
        <svg class="contact__icon" viewBox="0 0 24 24" aria-hidden="true"><path d="M2 5h20v2l-10 6L2 7z"/><path d="M2 9l10 6 10-6v10H2z"/></svg>
        <span>info@yourwebsite.com</span>
      </li>
      <li class="contact__item">
        <svg class="contact__icon" viewBox="0 0 24 24" aria-hidden="true"><path fill="none" stroke="#232250" stroke-width="2" d="M12 2a10 10 0 1 0 0 20a10 10 0 1 0 0-20zM2 12h20M12 2c3 3 3 17 0 20M12 2c-3 3-3 17 0 20"/></svg>
        <span>www.yourwebsite.com</span>
      </li>
    </ul>
  </section>

  <section class="card card--back" aria-label="Business card back">
    <div class="back-pattern" role="img" aria-label="Diagonal repeated brand-name pattern in muted navy"></div>
    <div class="back-wordmark">Pexla</div>
  </section>
</main>
</body>
</html>
```